Distribution company for alcoholic beverages called Amber Crestline needs a web design

1. We would like to first page to show

A. The company logo (in att)

B. A wall of bottles similar to
- www.underpaperskies.com that will click through to the brand info
- https://keltaronworks.com/brands/
PLEASE NOTE THAT IT CAN NOT BE THE SAME DESIGN - it needs to have a different look and feel ... this is to show what we mean with a wall of bottles

Important = we need to be able to keep adding new bottles/brands over time

C. only 3 tabs needed – Brands, About Us and Contact

Style
- simple and clean
- colourful
- classy

2. Page 2
The intro page to describe the company
we can use the same (Box + drop) logo to create a visual

3. Page 3
The referral page to the specific brands/company
= we need to alternating versions of this / just different ordering in the page

Target Market(s)

importers, brand owners, bartenders,

Industry/Entity Type

It Company

Number of Pages Required

3 page

Requirements
Must have
• A landing page visual that can display bottles we will sell in an organised way
• We need to be able to add bottles when the portfolio expands
Nice to have
• to have the drop out of the logo as a part of the design of the website

```html
<!DOCTYPE html>
<html lang="en">
<head>
<meta charset="utf-8">
<title>Amber Crestline</title>
<link href="https://fonts.googleapis.com/css2?family=Oswald:wght@400;500&family=Open+Sans:wght@400&display=swap" rel="stylesheet">
<style>
:root{
  --ink:#1f1f1f;
  --nav:#333;
  --tile-dark:#e4e4e4;
  --tile-light:#f0f0f0;
  --footer:#e9e9e9;
  --muted:#555;
  --icon:#8a8a8a;
  --button:#3a3a3a;
}
*{margin:0;padding:0;box-sizing:border-box}
html,body{width:1200px;height:843px;overflow:hidden;background:#fff}
body{position:relative;font-family:'Open Sans',sans-serif;color:var(--ink)}
.site-header{height:99px;position:relative}
.brand-mark{position:absolute;left:26px;top:34px;width:145px;height:40px;border:2px solid var(--ink);display:flex;align-items:center;justify-content:center;gap:6px;font-family:'Oswald',sans-serif;font-weight:500;font-size:14px;letter-spacing:1px;color:var(--ink);text-transform:uppercase}
.brand-mark .dot{width:9px;height:9px;border-radius:50%;background:var(--ink)}
.main-nav{position:absolute;right:24px;top:40px;display:flex;gap:32px}
.main-nav a{font-family:'Oswald',sans-serif;font-size:19px;line-height:28px;color:var(--nav);text-decoration:none;text-transform:uppercase;letter-spacing:-.2px}
.bottle-wall{display:grid;grid-template-columns:repeat(5,1fr);grid-auto-rows:192px;gap:3px;width:1200px}
.tile{position:relative;display:flex;align-items:center;justify-content:center;background:var(--tile-light)}
.tile.dark{background:var(--tile-dark)}
.bottle{display:block}
.tile-overlay{position:absolute;inset:0;display:flex;flex-direction:column;align-items:center;justify-content:center;padding-bottom:22px}
.tile-title{font-family:'Oswald',sans-serif;font-weight:500;font-size:28px;line-height:36px;color:var(--ink);text-transform:uppercase;letter-spacing:-.5px}
.tile-button{margin-top:2px;background:var(--button);color:#fff;font-size:10px;text-transform:uppercase;padding:7px 14px}
.faded{opacity:.35}
.contact-strip{height:67px;display:flex;align-items:center;justify-content:center;gap:12px;font-family:'Oswald',sans-serif;font-size:20px;color:var(--ink)}
.contact-strip span{display:flex;align-items:center;gap:5px}
.site-footer{position:absolute;left:0;right:0;bottom:0;height:97px;background:var(--footer)}
.footer-links{position:absolute;left:23px;top:28px;font-size:11px;color:var(--muted)}
.footer-links a{color:var(--muted);text-decoration:none}
.footer-links .sep{margin:0 9px}
.copyright{position:absolute;left:23px;top:54px;font-size:11px;color:var(--muted)}
.social{position:absolute;right:28px;top:38px;display:flex;gap:20px;align-items:center}
.social a{font-family:'Oswald',sans-serif;font-size:14px;color:var(--icon);text-decoration:none}
</style>
</head>
<body>
<header class="site-header">
  <div class="brand-mark"><span class="dot"></span>Amber Crestline</div>
  <nav class="main-nav"><a href="#">Brands</a><a href="#">About us</a><a href="#">Contact</a></nav>
</header>

<main class="bottle-wall">
  <a class="tile dark">
    <svg class="bottle faded" role="img" aria-label="Clear rum bottle" width="32" height="145" viewBox="0 0 100 200" preserveAspectRatio="none"><defs><linearGradient id="g1" x1="0" x2="1"><stop offset="0" stop-color="#bbb"/><stop offset=".5" stop-color="#e6e6e6"/><stop offset="1" stop-color="#bbb"/></linearGradient></defs><path d="M42 0H58V40C58 60 80 65 80 85V192Q80 200 72 200H28Q20 200 20 192V85C20 65 42 60 42 40Z" fill="url(#g1)"/></svg>
    <div class="tile-overlay"><div class="tile-title">Tessel Rum</div><div class="tile-button">View more</div></div>
  </a>
  <a class="tile"><svg class="bottle" role="img" aria-label="Green beer bottle" width="44" height="148" viewBox="0 0 100 200" preserveAspectRatio="none"><defs><linearGradient id="g2" x1="0" x2="1"><stop offset="0" stop-color="#1f6b14"/><stop offset=".5" stop-color="#48b72c"/><stop offset="1" stop-color="#1f6b14"/></linearGradient></defs><path d="M42 0H58V40C58 60 80 65 80 85V192Q80 200 72 200H28Q20 200 20 192V85C20 65 42 60 42 40Z" fill="url(#g2)"/></svg></a>
  <a class="tile dark"><svg class="bottle" role="img" aria-label="Gold tequila bottle" width="52" height="132" viewBox="0 0 100 200" preserveAspectRatio="none"><defs><linearGradient id="g3"><stop offset="0" stop-color="#e8c48a"/><stop offset="1" stop-color="#d99c56"/></linearGradient></defs><path d="M40 0H60V30C60 38 88 40 88 55V192Q88 200 80 200H20Q12 200 12 192V55C12 40 40 38 40 30Z" fill="url(#g3)"/></svg></a>
  <a class="tile"><svg class="bottle" role="img" aria-label="Clear vodka bottle" width="52" height="124" viewBox="0 0 100 200" preserveAspectRatio="none"><defs><linearGradient id="g4" x2="0" y2="1"><stop offset="0" stop-color="#c9c29a"/><stop offset=".25" stop-color="#e8e8e8"/><stop offset="1" stop-color="#d6d6d6"/></linearGradient></defs><path d="M40 0H60V30C60 38 88 40 88 55V192Q88 200 80 200H20Q12 200 12 192V55C12 40 40 38 40 30Z" fill="url(#g4)"/></svg></a>
  <a class="tile dark"><svg class="bottle" role="img" aria-label="Dark red wine bottle" width="28" height="116" viewBox="0 0 100 200" preserveAspectRatio="none"><defs><linearGradient id="g5" x1="0" x2="1"><stop offset="0" stop-color="#1a0a0c"/><stop offset=".5" stop-color="#4a1a20"/><stop offset="1" stop-color="#1a0a0c"/></linearGradient></defs><path d="M40 0H60V50C60 62 88 62 88 78V192Q88 200 80 200H20Q12 200 12 192V78C12 62 40 62 40 50Z" fill="url(#g5)"/></svg></a>

  <a class="tile"><svg class="bottle" role="img" aria-label="Red wine bottle" width="32" height="132" viewBox="0 0 100 200" preserveAspectRatio="none"><defs><linearGradient id="g6" x2="0" y2="1"><stop offset="0" stop-color="#6b1622"/><stop offset=".3" stop-color="#222"/><stop offset="1" stop-color="#1a1a1a"/></linearGradient></defs><path d="M40 0H60V50C60 62 88 62 88 78V192Q88 200 80 200H20Q12 200 12 192V78C12 62 40 62 40 50Z" fill="url(#g6)"/></svg></a>
  <a class="tile dark"><svg class="bottle" role="img" aria-label="Flask of amber spirit" width="56" height="116" viewBox="0 0 100 200" preserveAspectRatio="none"><defs><linearGradient id="g7" x2="0" y2="1"><stop offset="0" stop-color="#ddd"/><stop offset=".55" stop-color="#c98e6c"/><stop offset="1" stop-color="#b77a4a"/></linearGradient></defs><path d="M40 0H60V30C60 38 88 40 88 55V192Q88 200 80 200H20Q12 200 12 192V55C12 40 40 38 40 30Z" fill="url(#g7)"/></svg></a>
  <a class="tile"><svg class="bottle" role="img" aria-label="Wide cognac decanter" width="100" height="140" viewBox="0 0 100 200" preserveAspectRatio="none"><defs><linearGradient id="g8" x2="0" y2="1"><stop offset="0" stop-color="#4a2a10"/><stop offset=".35" stop-color="#e07a1c"/><stop offset="1" stop-color="#b84c0c"/></linearGradient></defs><path d="M38 0H62V30C62 40 96 45 96 70V188Q96 200 84 200H16Q4 200 4 188V70C4 45 38 40 38 30Z" fill="url(#g8)"/></svg></a>
  <a class="tile dark"><svg class="bottle" role="img" aria-label="Brown beer bottle" width="36" height="136" viewBox="0 0 100 200" preserveAspectRatio="none"><defs><linearGradient id="g9" x1="0" x2="1"><stop offset="0" stop-color="#3a1d08"/><stop offset=".5" stop-color="#a45a1a"/><stop offset="1" stop-color="#3a1d08"/></linearGradient></defs><path d="M42 0H58V40C58 60 80 65 80 85V192Q80 200 72 200H28Q20 200 20 192V85C20 65 42 60 42 40Z" fill="url(#g9)"/></svg></a>
  <a class="tile"><svg class="bottle" role="img" aria-label="Round brandy bottle" width="48" height="152" viewBox="0 0 100 200" preserveAspectRatio="none"><defs><linearGradient id="g10" x2="0" y2="1"><stop offset="0" stop-color="#222"/><stop offset=".35" stop-color="#d08018"/><stop offset="1" stop-color="#7a1408"/></linearGradient></defs><path d="M40 0H60V40C60 60 95 110 95 170Q95 200 70 200H30Q5 200 5 170C5 110 40 60 40 40Z" fill="url(#g10)"/></svg></a>

  <a class="tile dark"><svg class="bottle" role="img" aria-label="Golden whisky bottle" width="52" height="136" viewBox="0 0 100 200" preserveAspectRatio="none"><defs><linearGradient id="g11" x2="0" y2="1"><stop offset="0" stop-color="#333"/><stop offset=".2" stop-color="#e8b83a"/><stop offset="1" stop-color="#c98a10"/></linearGradient></defs><path d="M40 0H60V30C60 38 88 40 88 55V192Q88 200 80 200H20Q12 200 12 192V55C12 40 40 38 40 30Z" fill="url(#g11)"/></svg></a>
  <a class="tile"><svg class="bottle" role="img" aria-label="Dark cola bottle" width="32" height="128" viewBox="0 0 100 200" preserveAspectRatio="none"><defs><linearGradient id="g12" x1="0" x2="1"><stop offset="0" stop-color="#1a0a06"/><stop offset=".5" stop-color="#5a2414"/><stop offset="1" stop-color="#1a0a06"/></linearGradient></defs><path d="M42 0H58V40C58 60 80 65 80 85V192Q80 200 72 200H28Q20 200 20 192V85C20 65 42 60 42 40Z" fill="url(#g12)"/></svg></a>
  <a class="tile dark"><svg class="bottle" role="img" aria-label="Amber liqueur bottle" width="52" height="140" viewBox="0 0 100 200" preserveAspectRatio="none"><defs><linearGradient id="g13" x2="0" y2="1"><stop offset="0" stop-color="#222"/><stop offset=".22" stop-color="#d08a20"/><stop offset="1" stop-color="#8a2a0c"/></linearGradient></defs><path d="M40 0H60V30C60 38 88 40 88 55V192Q88 200 80 200H20Q12 200 12 192V55C12 40 40 38 40 30Z" fill="url(#g13)"/></svg></a>
  <a class="tile"><svg class="bottle" role="img" aria-label="Red spirit decanter" width="68" height="132" viewBox="0 0 100 200" preserveAspectRatio="none"><defs><linearGradient id="g14" x2="0" y2="1"><stop offset="0" stop-color="#222"/><stop offset=".2" stop-color="#d8461a"/><stop offset="1" stop-color="#a8140a"/></linearGradient></defs><path d="M40 0H60V40C60 60 95 110 95 170Q95 200 70 200H30Q5 200 5 170C5 110 40 60 40 40Z" fill="url(#g14)"/></svg></a>
  <a class="tile dark"><svg class="bottle" role="img" aria-label="Wicker wrapped wine flask" width="68" height="136" viewBox="0 0 100 200" preserveAspectRatio="none"><defs><linearGradient id="g15" x2="0" y2="1"><stop offset="0" stop-color="#3e6e2a"/><stop offset=".45" stop-color="#1e2e14"/><stop offset=".6" stop-color="#a07a44"/><stop offset="1" stop-color="#7a5a2e"/></linearGradient></defs><path d="M40 0H60V40C60 60 95 110 95 170Q95 200 70 200H30Q5 200 5 170C5 110 40 60 40 40Z" fill="url(#g15)"/></svg></a>
</main>

<section class="contact-strip">
  <span><svg width="11" height="18" viewBox="0 0 11 18"><rect x="1" y="1" width="9" height="16" rx="1.5" fill="none" stroke="#1f1f1f" stroke-width="2"/><rect x="3" y="3" width="5" height="9" fill="#1f1f1f"/></svg>555 210 4873</span>
  <span>/</span>
  <span><svg width="20" height="15" viewBox="0 0 20 15"><rect width="20" height="15" rx="1.5" fill="#1f1f1f"/><path d="M1 2l9 6 9-6" fill="none" stroke="#fff" stroke-width="1.5"/></svg>hello@ambercrestline.com</span>
</section>

<footer class="site-footer">
  <div class="footer-links"><a href="#">Brands</a><span class="sep">|</span><a href="#">About us</a><span class="sep">|</span><a href="#">Contact</a></div>
  <div class="copyright">Copyright © 2018 Amber Crestline. All rights reserved.</div>
  <div class="social">
    <a href="#">Murmur</a><a href="#">Vistaly</a><a href="#">Reelhub</a><a href="#">Linkora</a><a href="#">Starly</a>
    <svg width="24" height="18" viewBox="0 0 24 18"><rect width="24" height="18" rx="2" fill="#8a8a8a"/><path d="M1 2l11 8 11-8" fill="none" stroke="#e9e9e9" stroke-width="1.6"/></svg>
  </div>
</footer>
</body>
</html>
```